We are creating the packaging for our premium gift box: “Velmora Links Collection.”
This box contains a green fee for two people, valid at the recipient’s choice of one of the most exclusive and scenic golf courses in Italy.
• Box dimensions: 16x16 x 2 cm
• Label coverage: The design must wrap around the two large square sides and the two lateral edges, similar to Brevlo packaging.
• Style: Elegant, refined, and modern.

Front design:
• A strong emotional golf image (luxury golf course setting, Italian landscape, or moment of play).
• Title: “Velmora Links Collection”.
• It must be clearly visible that the box includes a round of golf for two people in one of the 50 most exclusive and scenic golf courses in Italy.

Back design:
The back should contain the following text:

Discover Italy’s most iconic golf courses
With this gift box you and a guest can enjoy a round of golf at your choice of one of the 20 most beautiful courses in Italy. From championship layouts to breathtaking landscapes, every round is an unforgettable experience.

Some of the included courses:
• Tessaro Vinelli Golf Club, Rome (host of the Harwick Trophy 2023)
• Grand Lawn Le Betulle, Turin
• Calvessa Resort, Sicily
• Circolo Golf Villa Morandi, Lake Como
• Sulimo Golf Club, Costa Smeralda
• Brunello Golf Club, Tuscany
• Golf Club Rocchetavina, Piedmont

…and many more top-ranked Italian destinations.

How it works:
1. Choose your preferred golf course from the list.
2. Book directly with the club, using the code provided inside the box.
3. Enjoy an exclusive round of golf for two people.

This gift box offers flexibility, freedom, and access to Velmora's quiet fairway experiences — the perfect present for any passionate golfer.

The overall design should capture the prestige of Italian golf and communicate that this is the most desired gift for golf lovers.

Target Market(s)

Our target market is golf enthusiasts, gift buyers, and people looking for premium experience gifts. The typical buyer is between 30–60 years old, often purchasing for friends, family, or business partners. The gift should feel aspirational, elegant, and special — the perfect present for any golfer.

Industry/Entity Type

Gift boxes and experience packages, with a specific focus on golf and premium leisure experiences.

Font styles to use
Serif

Requirements
Must have
• A premium, elegant box design (21x21x2 cm) in line with luxury gift standards. • Emotional, high-quality golf imagery that immediately conveys the excitement of playing golf. • Clear and stylish branding of TeeParcel. • A design style inspired by Brevlo (label wrapping front + two sides + back). • On the back: a list of included golf courses and simple instructions on how to use the gift box.
Nice to have
• Minimalist and modern style with clean lines. • Touches of copper or metallic accents for a premium feel. • A contemporary design aesthetic similar to Nordwin Golf or Kavesh. • Lifestyle imagery that conveys joy, elegance, and aspiration, not just golf action.
Should not have
• No cheap or cluttered visuals. • No heavy use of gold or champagne tones (avoid cliché luxury). • No cartoonish or overly playful styles. • No complex text-heavy design — clarity and elegance are key.

```html
<!DOCTYPE html>
<html lang="en">
<head>
<meta charset="utf-8">
<title>Velmora Links Collection – Box Wrap</title>
<link rel="stylesheet" href="https://fonts.googleapis.com/css2?family=Cormorant+Garamond:wght@500;600&family=EB+Garamond:wght@400;500&display=swap">
<style>
  :root {
    --page: #ececec;
    --forest: #1c3c15;
    --forest-tab: #234a1d;
    --gold: #c8901f;
    --gold-text: #d0962a;
    --ivory: #f4f1e6;
  }
  * { margin: 0; padding: 0; box-sizing: border-box; }
  html, body { width: 1200px; height: 1200px; overflow: hidden; background: var(--page); }
  .canvas { position: relative; width: 1200px; height: 1200px; }
  .wrap-net { position: absolute; left: 30px; top: 340px; width: 1140px; height: 521px; }

  .spine {
    position: absolute; top: 0; width: 50px; height: 521px;
    background: var(--forest); border: 1px solid var(--gold);
    display: flex; align-items: center; justify-content: center;
  }
  .spine--left { left: 0; }
  .spine--right { left: 570px; }
  .spine__title {
    font-family: "Cormorant Garamond", serif; font-weight: 500;
    color: var(--ivory); font-size: 24px; letter-spacing: 4px; white-space: nowrap;
  }
  .spine--left .spine__title { writing-mode: vertical-rl; }
  .spine--right .spine__title { writing-mode: vertical-rl; transform: rotate(180deg); }

  .front { position: absolute; left: 50px; top: 0; width: 520px; height: 521px; background: var(--gold); }
  .front__photo {
    position: absolute; left: 7px; top: 7px; right: 7px; bottom: 7px;
    background: linear-gradient(180deg, #8299bb 0%, #b8c4cf 25%, #e9e9dc 48%, #d8cf96 56%, #6f7f32 64%, #3c4a1d 78%, #23261b 100%);
  }
  .tab {
    position: absolute; left: 50%; transform: translateX(-50%);
    width: 128px; background: var(--forest-tab); color: var(--ivory);
    display: flex; align-items: center; justify-content: center;
    font-family: "Cormorant Garamond", serif; font-weight: 500;
  }
  .tab--top { top: 0; height: 41px; font-size: 14px; letter-spacing: 3px; }
  .tab--bottom { bottom: 0; height: 42px; font-size: 22px; letter-spacing: 4px; }
  .front__title {
    position: absolute; left: 0; right: 0; top: 112px; text-align: center;
    font-family: "Cormorant Garamond", serif; font-weight: 600; color: var(--forest);
    text-transform: uppercase; line-height: 1.05;
  }
  .front__title span { display: block; }
  .front__title .line-1 { font-size: 38px; letter-spacing: 8px; }
  .front__title .line-2 { font-size: 31px; letter-spacing: 5px; }
  .front__offer {
    position: absolute; left: 0; right: 0; top: 407px; text-align: center;
    font-family: "EB Garamond", serif; color: var(--gold-text);
    font-size: 12.5px; letter-spacing: 1px; line-height: 20px; text-transform: uppercase;
  }

  .back {
    position: absolute; left: 620px; top: 0; width: 520px; height: 521px;
    background: var(--forest); font-family: "EB Garamond", serif; color: var(--gold-text);
    text-transform: uppercase; text-align: center;
  }
  .info-box { position: absolute; border: 1px solid var(--gold); }
  .info-box--intro { left: 46px; top: 74px; width: 424px; height: 93px; padding: 10px 14px; }
  .info-box__heading { font-size: 12.5px; letter-spacing: 1px; }
  .info-box__body { margin-top: 10px; font-size: 8.2px; letter-spacing: .6px; line-height: 10.5px; }
  .band {
    position: absolute; left: 109px; top: 193px; width: 303px; height: 24px;
    background: var(--gold); color: var(--forest); font-size: 12px; letter-spacing: 1px;
    display: flex; align-items: center; justify-content: center;
  }
  .course-list { position: absolute; left: 0; right: 0; top: 226px; list-style: none; font-size: 8.6px; letter-spacing: .7px; line-height: 12.3px; }
  .info-box--steps { left: 46px; top: 348px; width: 428px; height: 98px; padding: 12px 10px; text-align: left; }
  .steps { list-style: none; margin-top: 8px; font-size: 8.2px; letter-spacing: .6px; line-height: 12.3px; }
</style>
</head>
<body>
<div class="canvas">
  <div class="wrap-net">
    <div class="spine spine--left"><span class="spine__title">VELMORA LINKS COLLECTION.</span></div>

    <section class="front">
      <div class="front__photo" role="img" aria-label="Two golfers on a seaside green at sunset, one holding the flag, with cliffs, sea and a bunker in the foreground"></div>
      <div class="tab tab--top">GOLF GIFT</div>
      <h1 class="front__title"><span class="line-1">Velmora</span><span class="line-2">Links Collection</span></h1>
      <p class="front__offer">Round of golf for two people<br>in one of the 50 most exclusive<br>and scenic golf courses</p>
      <div class="tab tab--bottom">ITALY.</div>
    </section>

    <div class="spine spine--right"><span class="spine__title">VELMORA LINKS COLLECTION.</span></div>

    <section class="back">
      <div class="info-box info-box--intro">
        <h2 class="info-box__heading">Discover Italy’s most iconic golf courses</h2>
        <p class="info-box__body">With this gift box you and a guest can enjoy a round of golf at your choice of one of the 20 most beautiful courses in Italy. From championship layouts to breathtaking landscapes, every round is an unforgettable experience.</p>
      </div>
      <div class="band">Some of the included courses:</div>
      <ul class="course-list">
        <li>• Tessaro Vinelli Golf Club, Rome (host of the Harwick Trophy 2023)</li>
        <li>• Grand Lawn Le Betulle, Turin</li>
        <li>• Calvessa Resort, Sicily</li>
        <li>• Circolo Golf Villa Morandi, Lake Como</li>
        <li>• Sulimo Golf Club, Costa Smeralda</li>
        <li>• Brunello Golf Club, Tuscany</li>
        <li>• Golf Club Rocchetavina, Piedmont</li>
        <li>…and many more top-ranked Italian destinations.</li>
      </ul>
      <div class="info-box info-box--steps">
        <h2 class="info-box__heading">How it works:</h2>
        <ol class="steps">
          <li>1. Choose your preferred golf course from the list.</li>
          <li>2. Book directly with the club, using the code provided inside the box.</li>
          <li>3. Enjoy an exclusive round of golf for two people.</li>
        </ol>
      </div>
    </section>
  </div>
</div>
</body>
</html>
```